Disposable coffee cup design for restaurant cafe

# Quillet Coffee Cup Design Brief

## Project

Create a premium disposable coffee cup design for **Quillet Bar & Grill at la Vireto Desert Club** located in **Borrego Springs, California**.

LOGO IS ATTACHED

The design should reflect the feeling of a **modern desert retreat** that blends **mid-century modern design, vintage national park graphics, and upscale resort hospitality.** The cup should feel timeless, collectible, and instantly recognizable.

---

## Brand Personality

The cup should communicate:

* Warm and welcoming
* Authentic desert hospitality
* Mid-century modern elegance
* Adventure and exploration
* Quality handcrafted coffee
* Premium golf and resort lifestyle
* The original desert hideaway

Avoid designs that feel corporate, generic coffee shop, or overly rustic.

---

## Overall Style

Think of a blend of:

* Vintage National Park posters
* Palm Springs mid-century architecture
* Joshua Tree / Anza-Borrego aesthetic
* Clean Scandinavian layout
* Modern boutique coffee roasters
* Simple luxury

Use plenty of negative space with bold graphic elements.

---

## Color Palette

Primary colors should include:

* Warm white or cream
* Desert sand
* Charcoal black
* Rust
* Burnt orange
* Terracotta
* Sage green
* Desert olive
* Warm brown
* Muted gold accents

The design should also work as a one-color print for economical production if needed.

---

## Graphic Elements

Incorporate subtle illustrations inspired by the Borrego Springs desert, such as:

* Ocotillo
* Saguaro or barrel cactus
* Agave
* Desert mountains
* Flowing sand dunes
* Desert sun
* Stars / Dark Sky imagery
* Vintage compass or topographic elements
* Golf-inspired details used sparingly
* Campfire or ember-inspired textures

Graphics should feel artistic rather than cartoonish.

---

## Typography

Typography should be clean and premium.

Recommended style:

* Mid-century sans serif
* Vintage condensed lettering
* Simple modern serif accents

Avoid overly decorative fonts.

---

## Front of Cup

Front should prominently feature:

* Quillet logo
* "la Vireto Desert Club"
* "Borrego Springs, California"

The logo should remain the primary focal point.

---

## Back of Cup

Include:

* quilletatlavireto.com
* Drink customization area:

* Decaf
* Shots
* Whole
* Skim
* Oat
* Half & Half
* Heavy Cream
* Custom
* Name line
* Cup size (12 oz, 16 oz, or 22 oz)
* "Caution: Hot Liquid"

Keep the customization area organized and easy for staff to mark.

---

## Sizes

Create coordinated artwork for:

* 12 oz
* 16 oz
* 22 oz

Artwork should maintain the same visual identity while scaling appropriately.

---

## Printing

Design should be production-friendly:

* Limited ink coverage
* Minimal gradients
* High contrast
* Easy registration
* Suitable for flexographic or offset cup printing

---

## Desired Customer Experience

The cup should feel like something guests want to photograph and keep. It should evoke memories of:

* Morning coffee before a round of golf
* Desert sunrise
* Weekend road trips
* National park adventures
* Relaxing on the clubhouse patio
* Premium resort hospitality

The goal is to create a cup that reinforces the Quillet brand as a distinctive destination rather than just another coffee shop.

## Deliverables Requested

* Full-wrap cup artwork
* Front and back layouts
* 12 oz, 16 oz, and 22 oz production files
* CMYK and one-color versions
* Vector artwork (Adobe Illustrator)
* Print-ready PDF with bleed and dielines
* Color specifications and font references

```html
<!DOCTYPE html>
<html lang="en">
<head>
<meta charset="utf-8">
<title>Quillet Bar &amp; Grill – Coffee Cup Wrap</title>
<link rel="stylesheet" href="https://fonts.googleapis.com/css2?family=Barlow+Condensed:wght@600&family=Montserrat:wght@600&family=Source+Sans+3:wght@400&display=swap">
<style>
  :root {
    --page: #ffffff;
    --charcoal-wall: #625f57;
    --sun-cream: #fcf1b8;
    --ink: #211e1f;
    --sage-ground: #9ab688;
    --desert-rock: #7a6f60;
    --desert-sand: #d9b57a;
    --scrub-green: #7fa06a;
  }
  * { margin: 0; padding: 0; box-sizing: border-box; }
  html, body {
    width: 924px;
    height: 1200px;
    overflow: hidden;
    background: var(--page);
  }
  .cup-wrap {
    position: absolute;
    left: 52px;
    top: 320px;
    width: 820px;
    height: 561px;
    overflow: hidden;
  }
  .wrap-art {
    position: absolute;
    inset: 0;
    width: 820px;
    height: 561px;
    display: block;
  }
  .brand-name {
    position: absolute;
    left: 0;
    width: 820px;
    text-align: center;
    font-family: "Montserrat", sans-serif;
    font-weight: 600;
    color: var(--ink);
    text-transform: uppercase;
  }
  .brand-name--main {
    top: 104px;
    font-size: 30px;
    letter-spacing: 0.2em;
    padding-left: 0.2em;
  }
  .brand-name--sub {
    top: 154px;
    font-size: 10.5px;
    letter-spacing: 0.28em;
    padding-left: 0.28em;
  }
  .drink-title {
    position: absolute;
    left: 0;
    top: 150px;
    width: 820px;
    text-align: center;
    font-family: "Barlow Condensed", sans-serif;
    font-weight: 600;
    font-size: 172px;
    line-height: 1;
    color: var(--ink);
    letter-spacing: -0.01em;
  }
  .cup-size {
    position: absolute;
    left: 0;
    width: 820px;
    text-align: center;
    font-family: "Source Sans 3", sans-serif;
    font-weight: 400;
    color: var(--ink);
    line-height: 1;
  }
  .cup-size--oz { top: 340px; font-size: 27px; left: 2px; }
  .cup-size--ml { top: 368px; font-size: 14px; }
</style>
</head>
<body>
  <main class="cup-wrap">
    <svg class="wrap-art" viewBox="0 0 820 561" xmlns="http://www.w3.org/2000/svg">
      <rect class="wall" x="0" y="0" width="820" height="561" fill="var(--charcoal-wall)"/>
      <circle class="desert-sun" cx="409" cy="262" r="218" fill="var(--sun-cream)"/>
      <defs>
        <linearGradient id="desert-scene-tone" x1="0" y1="0" x2="0" y2="1">
          <stop offset="0" stop-color="var(--desert-rock)" stop-opacity="0.55"/>
          <stop offset="0.6" stop-color="var(--desert-sand)" stop-opacity="0.55"/>
          <stop offset="1" stop-color="var(--scrub-green)"/>
        </linearGradient>
      </defs>
      <rect class="desert-scene" x="0" y="396" width="820" height="80"
            fill="url(#desert-scene-tone)" role="img"
            aria-label="Illustrated desert landscape: rocky mountains and spires, a flowering desert shrub, prickly pear cactus with pink blooms, agave and saguaro"/>
      <rect class="ground" x="0" y="473" width="820" height="88" fill="var(--sage-ground)"/>
    </svg>

    <p class="brand-name brand-name--main">Quillet</p>
    <p class="brand-name brand-name--sub">Bar &amp; Grill</p>

    <h1 class="drink-title">Coffee</h1>

    <p class="cup-size cup-size--oz">12oz</p>
    <p class="cup-size cup-size--ml">400ml</p>
  </main>
</body>
</html>
```